Business Card Design - ChoiceCraft

Looking for creative, modern design, two sided for ChoiceCraft that is consistent with color and feel of website www.choicecraftpro.net.
Updates

Back of card will be used to promote products or have a quote revolving around decisions, change, leadership, innovation, creativity. Back should also have space to promote website, but optional to use the icon. Front of the card will need to use the icon and have standard place for name, job title, phone and email. We are not looking to put a mailing address or fax. Also want space to place a few words/phrase explaining what we do...such as individual growth and organizational development or tools, training, information...in addition, want the facebook icon small on the front somewhere as we are also on facebook.

Vector file uploaded of icon.

Target Market(s)

Professional coaching for individual growth and organizational development

Industry/Entity Type

Business

Requirements
Must have
• Icon...see attached.

```html
<!DOCTYPE html>
<html lang="en">
<head>
<meta charset="utf-8">
<title>ChoiceCraft Business Card</title>
<link rel="stylesheet" href="https://fonts.googleapis.com/css2?family=Arimo:wght@400;700&display=swap">
<style>
  :root {
    --stage: #d9dadc;
    --card: #ffffff;
    --ink: #1f1f1f;
    --ink-soft: #333333;
    --blue: #1fa3e0;
    --blue-deep: #0e5fae;
    --blue-light: #8fd0f2;
    --blue-pale: #e6f3fb;
    --white: #ffffff;
  }
  * { margin: 0; padding: 0; box-sizing: border-box; }
  html, body { width: 1200px; height: 1123px; overflow: hidden; }
  body {
    background: var(--stage);
    font-family: "Arimo", Arial, sans-serif;
    color: var(--ink);
    position: relative;
  }
  .card {
    position: absolute;
    width: 844px;
    height: 480px;
    background: var(--card);
    overflow: hidden;
    box-shadow: 0 2px 6px rgba(0,0,0,.18);
  }
  .card--front { left: 67px; top: 56px; }
  .card--back { left: 291px; top: 578px; width: 841px; }

  /* front */
  .front-wave { position: absolute; left: 0; top: 0; }
  .brand-mark {
    position: absolute; left: 146px; top: 20px;
    width: 168px; height: 168px; border-radius: 50%;
    background: radial-gradient(circle at 45% 40%, #eef4f9 0%, #b9c8d6 60%, #1f8fd6 100%);
  }
  .brand-name {
    position: absolute; left: 0; width: 484px; top: 240px;
    text-align: center; font-weight: 700; font-size: 33px; letter-spacing: 1px;
    color: var(--ink);
  }
  .tagline {
    position: absolute; left: 0; width: 484px; top: 306px;
    text-align: center; font-size: 22px; line-height: 29px; color: var(--ink-soft);
  }
  .person { position: absolute; right: 26px; top: 38px; text-align: right; }
  .person__name { font-weight: 700; font-size: 33px; letter-spacing: .5px; }
  .person__title { font-size: 23px; margin-top: 4px; color: var(--ink-soft); }
  .contacts {
    position: absolute; right: 26px; top: 335px;
    list-style: none; text-align: right; color: var(--white); font-size: 23px; line-height: 29.5px;
  }
  .contacts li { display: flex; justify-content: flex-end; align-items: center; gap: 9px; }
  .contacts svg { flex: none; }
  .social-dot { width: 13px; height: 13px; background: var(--white); border-radius: 2px; }

  /* back */
  .back-mark {
    position: absolute; left: 300px; top: 90px; width: 300px; height: 300px;
    border-radius: 50%; background: var(--blue-pale); opacity: .6;
  }
  .quotes { position: absolute; left: 0; top: 0; list-style: none; }
  .quote { position: absolute; left: 0; width: 841px; }
  .quote__dot {
    position: absolute; left: 47px; top: 4px; width: 32px; height: 32px; border-radius: 50%;
    background: radial-gradient(circle at 45% 40%, #eef4f9 0%, #a9bfd2 60%, #1f8fd6 100%);
  }
  .quote__text {
    position: absolute; left: 96px; top: 0; font-size: 22px; color: var(--ink-soft); white-space: nowrap;
  }
  .quote__text::before {
    content: "\201C"; font-family: Georgia, serif; font-weight: 700; font-size: 34px; color: var(--ink);
    position: relative; top: 4px; margin-right: 4px;
  }
  .quote__text::after {
    content: "\201D"; font-family: Georgia, serif; font-weight: 700; font-size: 34px; color: var(--ink);
    position: relative; top: 16px; margin-left: 2px;
  }
  .quote__author {
    position: absolute; left: 119px; top: 34px; font-weight: 700; font-size: 22px; color: var(--blue);
  }
  .quote:nth-child(1) { top: 44px; }
  .quote:nth-child(2) { top: 128px; }
  .quote:nth-child(3) { top: 211px; }
  .quote:nth-child(4) { top: 296px; }
  .quote:nth-child(5) { top: 381px; }
</style>
</head>
<body>

<section class="card card--front">
  <svg class="front-wave" width="844" height="480" viewBox="0 0 844 480" aria-hidden="true">
    <defs>
      <linearGradient id="waveFill" x1="0" y1="0" x2="1" y2="0">
        <stop offset="0" stop-color="#a9dcf5"/>
        <stop offset=".55" stop-color="#4bb7ea"/>
        <stop offset="1" stop-color="#1fa3e0"/>
      </linearGradient>
    </defs>
    <path d="M0 370 C 230 470 520 330 844 205 L844 480 L0 480 Z" fill="url(#waveFill)"/>
    <path d="M0 380 C 180 440 420 400 844 235" fill="none" stroke="#0e5fae" stroke-width="7"/>
    <path d="M0 400 C 200 460 470 400 844 250" fill="none" stroke="#ffffff" stroke-width="9"/>
    <path d="M70 430 C 260 470 420 420 560 370" fill="none" stroke="#1679c4" stroke-width="6"/>
    <path d="M0 450 C 170 500 360 470 520 410" fill="none" stroke="#ffffff" stroke-width="5"/>
  </svg>

  <div class="brand-mark" role="img" aria-label="ChoiceCraft emblem area"></div>
  <div class="brand-name">ChoiceCraft</div>
  <p class="tagline">Supporting individual growth<br>and&nbsp; organizational development.</p>

  <div class="person">
    <div class="person__name">Your Name</div>
    <div class="person__title">Title</div>
  </div>

  <ul class="contacts">
    <li>
      <svg width="16" height="16" viewBox="0 0 16 16" aria-hidden="true"><path d="M4 1 L6.5 5 L5 6.5 C6 9 7 10 9.5 11 L11 9.5 L15 12 L13 15 C7 15 1 9 1 3 Z" fill="#fff"/></svg>
      123-456-789
    </li>
    <li>
      <svg width="16" height="13" viewBox="0 0 16 13" aria-hidden="true"><rect x="1" y="1" width="14" height="11" fill="none" stroke="#fff" stroke-width="2"/><path d="M1 1 L8 7 L15 1" fill="none" stroke="#fff" stroke-width="2"/></svg>
      hello@choicecraftpro.net
    </li>
    <li>
      <svg width="16" height="16" viewBox="0 0 16 16" aria-hidden="true"><circle cx="8" cy="8" r="6.5" fill="none" stroke="#fff" stroke-width="1.6"/><path d="M1.5 8 H14.5 M8 1.5 C5 5 5 11 8 14.5 M8 1.5 C11 5 11 11 8 14.5" fill="none" stroke="#fff" stroke-width="1.3"/></svg>
      www.choicecraftpro.net
    </li>
    <li><span class="social-dot"></span>/choicecraftpro</li>
  </ul>
</section>

<section class="card card--back">
  <div class="back-mark" aria-hidden="true"></div>
  <ul class="quotes">
    <li class="quote"><span class="quote__dot"></span><span class="quote__text">Try not to become a man of success, but rather a man of value.</span><span class="quote__author">- Martin Hale</span></li>
    <li class="quote"><span class="quote__dot"></span><span class="quote__text">The only constant is change.</span><span class="quote__author">- Clara Voss</span></li>
    <li class="quote"><span class="quote__dot"></span><span class="quote__text">We are what we repeatedly do. Excellence is not an act, it is a habit.</span><span class="quote__author">- Theo Marsh</span></li>
    <li class="quote"><span class="quote__dot"></span><span class="quote__text">Simplicity is the ultimate sophistication.</span><span class="quote__author">- Rena Dalton</span></li>
    <li class="quote"><span class="quote__dot"></span><span class="quote__text">Life is not fair - get used to it.</span><span class="quote__author">- Owen Brooks</span></li>
  </ul>
</section>

</body>
</html>
```